Printed Circuit Board Company Web Site Design - Please see new file 82012 web design

We are a printed circuit board manufacturer. Need a company professional web site to allow our potential customers to know more about our background, capability and our products. The web site will contain three languages, which are Chinese, English and Japanese. Our audience are mainly electronic companies that procure printed circuit boards. I have a word document that have all the required text in all three languages. The final design should communicate the impression that we embrace quality, trustworthiness and long term partnership business principles.
We should have sections that allow us to post pictures of our facilities.
I have added the three files in three different languages.
Some of the information is below:
Background
RDV Harbourline Limited (RDV) was set up in Hong Kong in 2007 by two Hong Kong entrepreneurs, Mr. Tak Wong and Mr. Lok Fai. We acquired the single sided printed circuit board factory located in Dongguan City, Guangdong Province, China, from Tovand Corporation of the U.S. in 2007. In addition to RDV, Mr. Wong and Mr. Fai also own Halberd Technology Company Limited, a semiconductor company based in Hong Kong since 1997 with a total investment of over US$100 million. Halberd is engaged in the manufacturing of flexible substrates and MEMS assembly business.
RDV has been awarded TS 16949 and ISO14000 certificates since 2009 and 2004 respectively.
Business Principles
RDV Harbourline Limited strives to be a professional top notched printed circuit board supplier. We embrace four “EXCELLENCE” principles, namely, excellence in quality, excellence in prices, excellence in services and excellence in on time delivery.
We approach each customer with a long-term partnership view that delivers the lowest ownership costs and highest total values to our customers. We customize quotations and solutions in order to allow our customers to win more businesses. We believe by thinking from our customers’ points of view we will be able to create a WIN-WIN relationship.
Customers
Due to our excellent quality, services and production systems, RDV Harbourline Limited manage to service a number of large Japanese and US customers, which include:
Technical capability overview
Below is an overview of our current capability:
Target Market(s)
Electronic companies buyers
Industry/Entity Type
Business
Requirements
Must have
- Capability description
Should not have
- no cartoon

```html
<!DOCTYPE html>
<html lang="en">
<head>
<meta charset="utf-8">
<title>RDV Harbourline Limited</title>
<link href="https://fonts.googleapis.com/css2?family=Arvo:wght@700&family=Cinzel:wght@600&family=Dosis:wght@500&family=Pathway+Gothic+One&display=swap" rel="stylesheet">
<style>
:root{
  --green:#0f7a63;
  --green-dark:#0a5e4b;
  --green-light:#13876d;
  --orange:#f7931e;
  --orange-deep:#f26f21;
  --text:#4a4a4a;
  --grey-line:#c9c9c9;
  --field:#f2f2f2;
}
*{margin:0;padding:0;box-sizing:border-box}
html,body{width:1200px;height:1005px;overflow:hidden;background:#fff;font-family:Arial,Helvetica,sans-serif;color:var(--text)}
.page{position:relative;width:1200px;height:1005px}
.top-stripe{position:absolute;left:0;top:0;width:1200px;height:6px;background:var(--green)}
.brand{position:absolute;left:180px;top:20px;color:var(--green);font-family:Dosis,sans-serif;font-weight:500;line-height:1}
.brand-name{font-size:40px;letter-spacing:2px;display:flex;align-items:center;gap:8px}
.brand-name span.mark{width:12px;height:12px;background:var(--green);display:inline-block}
.brand-sub{font-size:14px;margin-top:2px;padding-left:6px}
.phone{position:absolute;left:860px;top:24px;display:flex;align-items:center;gap:6px;font-size:18px;color:#111}
.nav{position:absolute;left:0;top:85px;width:1200px;height:31px;background:linear-gradient(#13876d,#0a5e4b)}
.nav a{position:absolute;top:0;height:31px;line-height:32px;color:#fff;text-decoration:none;font-family:Cinzel,serif;font-weight:600;font-size:13px;letter-spacing:1px;text-align:center}
.nav .sep{position:absolute;top:0;width:1px;height:31px;background:rgba(255,255,255,.25)}
.login{position:absolute;left:956px;top:69px;width:62px;height:47px;background:linear-gradient(#ffa726,#f57c00);border-radius:4px 4px 0 0;color:#fff;font-weight:bold;font-size:12px;text-align:center;padding-top:6px}
.login svg{display:block;margin:0 auto 2px}
.hero{position:absolute;left:0;top:116px;width:1200px;height:259px;background:linear-gradient(90deg,#dcebf2,#f3f8fa 35%,#e8f1f5 100%);border-bottom:1px solid var(--grey-line)}
.hero-photo{position:absolute;left:540px;top:0;width:489px;height:259px;background:linear-gradient(90deg,rgba(243,248,250,0) 0%,#e4e9ec 14%,#d6dadc 40%,#cdd1d2 62%,#dcdfe0 82%,rgba(232,241,245,.4) 100%)}
.hero-copy{position:absolute;left:200px;top:20px;width:340px;font-family:"Pathway Gothic One",sans-serif;color:var(--green);font-size:25px;line-height:30px;text-align:center;letter-spacing:1px}
.hero-list{position:absolute;left:244px;top:121px;list-style:none;font-family:"Pathway Gothic One",sans-serif;color:var(--green);font-size:23px;letter-spacing:1px}
.hero-list li{height:31px;display:flex;align-items:center;gap:9px}
.welcome{position:absolute;left:178px;top:408px;width:530px}
.welcome h1{font-family:Dosis,sans-serif;font-weight:500;color:var(--orange);font-size:29px;margin-bottom:4px;white-space:nowrap}
.welcome p{font-size:12px;line-height:20.6px;text-align:justify}
.welcome p+p{margin-top:20.6px}
.quick{position:absolute;left:751px;top:407px;width:278px;height:291px;background:#e9e9e9;border:4px solid #fff;border-radius:22px;box-shadow:0 0 0 1px #ddd}
.quick-tab{position:absolute;left:29px;top:-3px;width:209px;height:53px;background:linear-gradient(#ff9b3a,var(--orange-deep));color:#fff;font-family:Arvo,serif;font-weight:700;font-size:19px;line-height:53px;text-align:center;letter-spacing:1.5px}
.field{position:absolute;left:25px;width:221px;height:30px;background:linear-gradient(#fafafa,var(--field));border:1px solid #d3d3d3;font-size:11.5px;color:#777;padding:8px 10px;letter-spacing:.5px}
.submit{position:absolute;left:179px;top:256px;width:67px;height:26px;background:var(--orange);color:#fff;font-family:Arvo,serif;font-weight:700;font-size:10px;letter-spacing:1px;line-height:26px;text-align:center}
.customers{position:absolute;left:178px;top:731px;width:849px;height:94px;border:1px solid var(--grey-line)}
.customers h2{position:absolute;left:14px;top:-20px;background:#fff;padding:0 8px;font-family:Dosis,sans-serif;font-weight:500;color:var(--orange);font-size:23px}
.logos{position:absolute;left:0;top:0;width:849px;height:94px;display:flex;align-items:center;justify-content:space-around;padding:0 16px}
.logos span{font-family:Dosis,sans-serif;font-weight:500;font-size:22px;color:#2f3b4c}
.arrow{position:absolute;top:764px}
.footer{position:absolute;left:0;top:849px;width:1200px;height:125px;background:linear-gradient(#117a63,#0d6a56);color:#fff}
.footer h3{position:absolute;left:178px;top:9px;font-size:11px;font-weight:bold}
.links{position:absolute;top:35px;list-style:none;font-size:9.5px;line-height:15.5px}
.links li::before{content:"\25B8";font-size:7px;margin-right:4px}
.address{position:absolute;right:178px;top:12px;text-align:right;font-size:9.5px;line-height:15.5px}
.address strong{font-size:11px}
.copyright{position:absolute;left:0;top:974px;width:1200px;height:31px;background:var(--green-dark);color:#fff;font-size:9.5px;font-weight:bold;text-align:center;line-height:29px}
</style>
</head>
<body>
<div class="page">
  <div class="top-stripe"></div>
  <div class="brand">
    <div class="brand-name"><span class="mark"></span>RDV</div>
    <div class="brand-sub">Harbourline Limited</div>
  </div>
  <div class="phone">
    <svg width="24" height="20" viewBox="0 0 24 20"><ellipse cx="12" cy="14" rx="11" ry="5" fill="#0f7a63"/><path d="M6 12c0-6 5-10 10-10 2 0 3 1 3 2l-3 3c-2-1-4 1-4 4" fill="none" stroke="#0f7a63" stroke-width="3" stroke-linecap="round"/></svg>
    <span>(852) 3920 4418</span>
  </div>

  <nav class="nav">
    <a href="#" style="left:188px;width:82px">HOME</a>
    <span class="sep" style="left:279px"></span>
    <a href="#" style="left:279px;width:130px">PRODUCTS</a>
    <span class="sep" style="left:409px"></span>
    <a href="#" style="left:409px;width:120px">SERVICES</a>
    <span class="sep" style="left:529px"></span>
    <a href="#" style="left:529px;width:230px">TECHNICAL CAPABILITIES</a>
    <span class="sep" style="left:759px"></span>
    <a href="#" style="left:759px;width:150px">CONTACT US</a>
    <span class="sep" style="left:909px"></span>
  </nav>
  <div class="login">
    <svg width="14" height="18" viewBox="0 0 14 18"><path d="M3 8V5a4 4 0 0 1 8 0v3" fill="none" stroke="#fff" stroke-width="2"/><rect x="1" y="8" width="12" height="9" rx="1" fill="#fff"/></svg>
    LOGIN
  </div>

  <section class="hero">
    <div class="hero-photo" role="img" aria-label="Photo of a business team of four gathered around an office meeting table by a bright window"></div>
    <div class="hero-copy">OUR PRINTED CIRCUIT BOARD<br>BUSINESS IS COMMITTED<br>TO “EXCELLENCE”</div>
    <ul class="hero-list">
      <li><svg width="22" height="16" viewBox="0 0 22 16"><path d="M1 9l6 5L21 1" fill="none" stroke="#0f7a63" stroke-width="3"/></svg>EXCELLENCE IN QUALITY</li>
      <li><svg width="22" height="16" viewBox="0 0 22 16"><path d="M1 9l6 5L21 1" fill="none" stroke="#0f7a63" stroke-width="3"/></svg>EXCELLENCE IN PRICES</li>
      <li><svg width="22" height="16" viewBox="0 0 22 16"><path d="M1 9l6 5L21 1" fill="none" stroke="#0f7a63" stroke-width="3"/></svg>EXCELLENCE IN SERVICES</li>
      <li><svg width="22" height="16" viewBox="0 0 22 16"><path d="M1 9l6 5L21 1" fill="none" stroke="#0f7a63" stroke-width="3"/></svg>EXCELLENCE IN ON TIME DELIVERY</li>
    </ul>
  </section>

  <section class="welcome">
    <h1>WELCOME TO RDV Harbourline Limited (RDV)</h1>
    <p>RDV Harbourline Limited (RDV) was set up in Hong Kong in 2007 by two Hong Kong entrepreneurs, Mr. Tak Wong and Mr. Lok Fai. We acquired the single sided printed circuit board factory located in Dongguan City, Guangdong Province, China, from Tovand Corporation of the U.S. in 2007. In addition to RDV, Mr. Wong and Mr. Fai also own Halberd Technology Company Limited, a semiconductor company based in Hong Kong since 1997 with a total investment of over US$100 million. Halberd is engaged in the manufacturing of flexible substrates and the assembly of Micro Electro Mechanical Systems (MEMS).</p>
    <p>RDV has been awarded TS16949 and ISO140001 since 2005 and 2004 respectively.</p>
  </section>

  <aside class="quick">
    <div class="quick-tab">QUICK CONTACT</div>
    <div class="field" style="top:55px">Name:</div>
    <div class="field" style="top:89px">Email:</div>
    <div class="field" style="top:124px">Company Name:</div>
    <div class="field" style="top:159px;height:86px">Comments:</div>
    <div class="submit">SUBMIT</div>
  </aside>

  <svg class="arrow" style="left:155px" width="18" height="20" viewBox="0 0 18 20"><path d="M14 2L5 10l9 8" fill="none" stroke="#bbb" stroke-width="4"/></svg>
  <section class="customers">
    <h2>OUR CUSTOMERS</h2>
    <div class="logos">
      <span>Verano</span>
      <span>Elmstead Power</span>
      <span>Korvane Energy</span>
      <span>NORU</span>
      <span>TOKIWA</span>
    </div>
  </section>
  <svg class="arrow" style="left:1032px" width="18" height="20" viewBox="0 0 18 20"><path d="M4 2l9 8-9 8" fill="none" stroke="#bbb" stroke-width="4"/></svg>

  <footer class="footer">
    <h3>POPULAR LINKS</h3>
    <ul class="links" style="left:178px">
      <li>Sitemap</li><li>Circuit Boardas</li><li>Capabilities</li><li>Industries Served</li><li>About Us</li>
    </ul>
    <ul class="links" style="left:320px">
      <li>Contact Us</li><li>Resources</li><li>Service Center</li><li>News &amp; Events</li><li>Privacy Policy</li>
    </ul>
    <div class="address">
      <strong>RDV Harbourline Limited</strong><br>
      28/F Marlow Tower<br>
      17 Kellet Road<br>
      Causeway Bay, HONG KONG<br>
      Telephone: (852)39204418<br>
      Fax: (852)39204419<br>
      Email: sales@rdvboard.com
    </div>
  </footer>
  <div class="copyright">COPYRIGHT © 2012 RDV HARBOURLINE LIMITED. ALL RIGHTS RESERVED</div>
</div>
</body>
</html>
```